Professional, Attractive, Simple Website Needed!!

We completed the design for our logo.

We need a website built out around this.

Here are a couple samples of how we want ours formatted.

http://brimvoltco.com

http://www.ravelbeam.com/lp/free-quote?LeadSource=Search%20Engine&ProgramName=searchads&experience=qual&language=en&type=brd&gclid=Xk7PLmqwTRZBNVuEYcaHdFgWsLoPeRtQnMxVbCzJaKiOuYtReWqAsDfGhJkLzXcVbNmQwErTyUiOpAsDfGhJkLzX_wcB

http://quorel.co
Updates

Project Deadline Extended
Reason: Extending this deadline due to our delay in providing designers with content for each page. This is coming in next 24 hours.

Project Deadline Extended
Reason: Due to scheduling conflicts and extended travel delays related to Puerto Rico, the deadline has been extended. Your patience is greatly appreciated.

Project Deadline Extended
Reason: Travel and scheduling conflicts have made it impossible to give this project the thorough review it deserves, therefore I am extending the deadline. Thank you for your patience!

Target Market(s)

Home Owners who earn 60k + household annually

Industry/Entity Type

It Professional

Coding

Coded - Design and coding required

Number of Pages Required

5+ page

Font styles to use
Serif

Colors
34a7d8
9bcb3c

Requirements
Must have
• Simple
• Lead form Entry (Ability for visitor to enter Name, number and address for a quote)
• Sleek Design
• Professional
• Testimonials
• Use color Scheme of Design Logo Attached
Nice to have
• Video when site starts
• Like this
• https://www.vidplexa.com/watch?v=Qm8rTbLw3Np&feature=vidplexa.be
Should not have
• Should not include Commercial solar
• Should not include wind power

```html
<!DOCTYPE html>
<html lang="en">
<head>
<meta charset="utf-8">
<title>Brightfield Energy</title>
<link rel="stylesheet" href="https://fonts.googleapis.com/css2?family=Josefin+Sans:wght@400;600;700&family=Open+Sans:ital,wght@0,400;0,600;0,700;1,400;1,600&display=swap">
<style>
:root{
  --blue:#34a7d8;
  --blue-deep:#2f8fcf;
  --green:#9bcb3c;
  --ink:#222;
  --body:#555;
  --muted:#888;
  --line:#ddd;
  --white:#fff;
}
*{box-sizing:border-box;margin:0;padding:0}
html,body{width:1200px;height:2835px;overflow:hidden}
body{font-family:"Open Sans",Arial,sans-serif;color:var(--body);background:var(--white);position:relative}
.heading{font-family:"Josefin Sans",Arial,sans-serif}
section,header,footer{position:absolute;left:0;width:1200px}

/* hero */
.hero{top:0;height:600px}
.hero-photo{position:absolute;inset:0 0 30px 0;background:linear-gradient(180deg,#4a5568 0%,#8a6a5a 20%,#d08458 30%,#5a6f8c 45%,#3f5673 70%,#4d6481 100%)}
.hero-curve{position:absolute;left:0;bottom:0;width:1200px;height:140px}
.brand{position:absolute;left:98px;top:26px;display:flex;align-items:center;gap:12px}
.brand-dot{width:22px;height:22px;border-radius:50%;background:var(--white)}
.brand-name{font-family:"Josefin Sans",Arial,sans-serif;font-weight:600;font-size:26px;color:var(--white);line-height:1}
.nav{position:absolute;right:92px;top:54px;display:flex;gap:34px;align-items:center;font-family:"Josefin Sans",Arial,sans-serif;font-size:16px;font-weight:600;color:var(--white);letter-spacing:.3px}
.nav .active{color:var(--green)}
.hero-title{position:absolute;top:142px;width:100%;text-align:center;font-size:52px;font-weight:600;color:var(--white);letter-spacing:1px}
.hero-sub{position:absolute;top:206px;width:100%;text-align:center;font-size:20px;font-weight:600;color:var(--white)}
.quote-form{position:absolute;left:284px;top:258px;width:632px;height:196px;background:rgba(40,40,40,.35)}
.field{position:absolute;height:37px;background:var(--white);font-size:12px;color:#666;padding:10px 14px}
.btn-quote{position:absolute;left:522px;top:380px;width:154px;height:47px;background:var(--green);color:var(--white);font-family:"Josefin Sans",Arial,sans-serif;font-weight:700;font-size:15px;display:flex;align-items:center;justify-content:center;border-radius:3px}
.play{position:absolute;left:578px;top:498px;width:44px;height:44px;border-radius:50%;background:#222}

/* buttons */
.btn-outline{position:absolute;width:160px;height:51px;border:1.5px solid #bbb;border-radius:4px;color:var(--green);font-family:"Josefin Sans",Arial,sans-serif;font-weight:700;font-size:15px;display:flex;align-items:center;justify-content:center;letter-spacing:.5px}

/* welcome */
.welcome{top:600px;height:421px}
.section-title{position:absolute;width:100%;text-align:center;font-size:32px;font-weight:600;color:var(--ink)}
.welcome p{position:absolute;top:162px;left:215px;width:770px;text-align:center;font-size:13.5px;line-height:29px;color:#666}

/* how it works */
.how{top:1021px;height:510px;background:linear-gradient(160deg,#3b9bd9 0%,#5ab0e4 35%,#3a98d6 70%,#4aa4dd 100%)}
.how .section-title{color:var(--white);top:64px}
.step{position:absolute;width:320px;text-align:center;color:var(--white)}
.step-ring{position:absolute;width:182px;height:182px;border:1.5px solid rgba(255,255,255,.75);border-radius:50%}
.step-num{position:absolute;width:38px;height:38px;border-radius:50%;background:var(--white);color:#222;font-weight:700;font-size:18px;display:flex;align-items:center;justify-content:center}
.step h3{position:absolute;top:356px;font-size:20px;font-weight:600}
.step p{position:absolute;top:395px;font-size:13.5px;line-height:26px}

/* why choose */
.why{top:1531px;height:539px}
.feature{position:absolute;width:240px;text-align:center}
.feature h3{font-family:"Josefin Sans",Arial,sans-serif;font-weight:600;font-size:20px;color:var(--ink);margin-top:0}
.feature p{font-size:12.5px;line-height:23px;color:#666;margin-top:12px}

/* testimonials */
.testimonials{top:2070px;height:374px;background:linear-gradient(180deg,#4a5060 0%,#8c7366 35%,#c98a5e 55%,#5c6478 75%,#3c4658 100%)}
.testimonial-panel{position:absolute;left:0;top:0}
.quote-label{position:absolute;left:98px;top:150px;font-size:34px;font-weight:600;color:var(--white);line-height:44px}
.avatar{position:absolute;left:526px;top:2118px;width:100px;height:100px;border-radius:50%;border:3px solid var(--white);background:linear-gradient(180deg,#9aa4ae,#5c6670)}
.testimonial-text{position:absolute;left:525px;top:180px;width:600px;font-size:15px;font-style:italic;line-height:31px;color:var(--white)}
.testimonial-name{position:absolute;left:525px;top:294px;font-size:15px;font-weight:700;color:var(--white)}
.dots{position:absolute;left:1062px;top:316px;display:flex;gap:4px}
.dots span{width:9px;height:9px;border-radius:50%;border:1.5px solid var(--white)}
.dots .on{background:var(--white)}

/* footer */
.site-footer{top:2444px;height:391px}
.footer-brand{position:absolute;left:98px;top:130px;display:flex;align-items:center;gap:12px}
.footer-brand .brand-dot{background:var(--blue)}
.footer-brand .brand-name{color:var(--blue);font-size:32px}
.col{position:absolute;top:92px}
.col h4{font-family:"Josefin Sans",Arial,sans-serif;font-weight:600;font-size:18px;color:var(--ink);margin-bottom:18px}
.col li{list-style:none;font-size:12px;line-height:21.5px;color:#444}
.col p{font-size:12px;line-height:21px;color:#444}
.email-field{width:255px;border-bottom:1px solid #ccc;font-size:11.5px;color:#999;padding:18px 0 8px 10px}
.btn-subscribe{margin-top:20px;width:104px;height:38px;background:var(--green);color:var(--white);font-size:11px;font-weight:700;display:flex;align-items:center;justify-content:center;border-radius:3px}
.contact-row{display:flex;gap:14px;font-size:12px;line-height:19px;color:#444;margin-bottom:16px}
.contact-row svg{flex:none;margin-top:3px}
.footer-rule{position:absolute;left:98px;top:310px;width:1004px;height:1px;background:var(--line)}
.copyright{position:absolute;left:98px;top:341px;font-size:11.5px;color:#444}
.social{position:absolute;left:974px;top:334px;display:flex;gap:8px}
.social span{width:26px;height:26px;border-radius:50%;border:1px solid var(--blue)}
</style>
</head>
<body>

<header class="hero">
  <div class="hero-photo" role="img" aria-label="Solar panel field at sunset under an orange and blue sky"></div>
  <svg class="hero-curve" viewBox="0 0 1200 140" preserveAspectRatio="none">
    <path d="M0 40 Q600 150 1200 40 L1200 140 L0 140 Z" fill="#fff"/>
    <path d="M0 40 Q600 150 1200 40 L1200 48 Q600 158 0 48 Z" fill="var(--blue)"/>
  </svg>
  <div class="brand"><span class="brand-dot"></span><span class="brand-name">Brightfield Energy</span></div>
  <nav class="nav">
    <span class="active">HOME</span><span>ABOUT</span><span>SERVICES</span><span>HOW IT WORKS</span><span>BLOG</span><span>RESOURCES</span><span>CONTACT</span>
    <svg width="14" height="14" viewBox="0 0 14 14"><circle cx="6" cy="6" r="4.5" fill="none" stroke="#fff" stroke-width="2"/><path d="M9.5 9.5 13 13" stroke="#fff" stroke-width="2"/></svg>
  </nav>
  <h1 class="hero-title heading">BRIGHTFIELD ENERGY</h1>
  <p class="hero-sub">Nemo enim ipsam voluptatem quia voluptas sit aspernatur aut odit</p>
  <div class="quote-form"></div>
  <div class="field" style="left:308px;top:280px;width:285px">Name</div>
  <div class="field" style="left:605px;top:280px;width:287px">Number</div>
  <div class="field" style="left:308px;top:329px;width:584px">Address</div>
  <div class="btn-quote">GET A QUOTE</div>
  <div class="play"><svg width="44" height="44" viewBox="0 0 44 44"><path d="M18 14 30 22 18 30Z" fill="#fff"/></svg></div>
</header>

<section class="welcome">
  <h2 class="section-title heading" style="top:100px">WELCOME TO BRIGHTFIELD ENERGY</h2>
  <p>At vero eos et accusamus et iusto odio dignissimos ducimus qui blanditiipr aesentium voluptatum deleniti at que corrupt. Quos dolores et quas molestias excepturi sint occaecati cupiditate non pro vident, similique sunt in culpa qui officia deserunt mollitia animi, id est lab orum et dolorum fdem rerum facilis est et expe.i</p>
  <div class="btn-outline" style="left:520px;top:271px">ABOUT US</div>
</section>

<section class="how">
  <h2 class="section-title heading">HOW IT WORKS</h2>

  <div class="step-ring" style="left:138px;top:141px"></div>
  <div class="step-ring" style="left:506px;top:141px"></div>
  <div class="step-ring" style="left:873px;top:141px"></div>
  <div class="step-num" style="left:291px;top:150px">1</div>
  <div class="step-num" style="left:659px;top:150px">2</div>
  <div class="step-num" style="left:1026px;top:150px">3</div>

  <svg style="position:absolute;left:199px;top:202px" width="60" height="60" viewBox="0 0 24 24"><path d="M6.6 10.8a15 15 0 0 0 6.6 6.6l2.2-2.2c.3-.3.7-.4 1-.2 1.1.4 2.3.6 3.6.6.6 0 1 .4 1 1V20c0 .6-.4 1-1 1A17 17 0 0 1 3 4c0-.6.4-1 1-1h3.5c.6 0 1 .4 1 1 0 1.3.2 2.5.6 3.6.1.3 0 .7-.2 1z" fill="var(--green)"/></svg>
  <svg style="position:absolute;left:567px;top:202px" width="60" height="60" viewBox="0 0 24 24"><rect x="3" y="5" width="15" height="15" rx="2" fill="none" stroke="var(--green)" stroke-width="2"/><path d="M19.5 2.5 22 5 13 14l-3.5 1 1-3.5z" fill="var(--green)"/></svg>
  <svg style="position:absolute;left:934px;top:202px" width="60" height="60" viewBox="0 0 24 24"><circle cx="12" cy="12" r="11" fill="var(--green)"/><path d="M6.5 12.5 10.5 16.5 17.5 8.5" fill="none" stroke="#3b9bd9" stroke-width="2.6"/></svg>

  <svg style="position:absolute;left:394px;top:212px" width="50" height="40" viewBox="0 0 50 40"><path d="M6 4 22 20 6 36M24 4 40 20 24 36" fill="none" stroke="rgba(255,255,255,.45)" stroke-width="6"/></svg>
  <svg style="position:absolute;left:760px;top:212px" width="50" height="40" viewBox="0 0 50 40"><path d="M6 4 22 20 6 36M24 4 40 20 24 36" fill="none" stroke="rgba(255,255,255,.45)" stroke-width="6"/></svg>

  <div class="step" style="left:69px"><h3 class="heading" style="width:320px">CONTACT</h3><p style="width:320px">Nam libero tempore, cum soluta nobis est eligendi optio cumque nihil imp</p></div>
  <div class="step" style="left:437px"><h3 class="heading" style="width:320px">DESIGN</h3><p style="width:320px">Nam libero tempore, cum soluta nobis est eligendi optio cumque nihil imp</p></div>
  <div class="step" style="left:804px"><h3 class="heading" style="width:320px">SCHEDULE &amp; INSTALL</h3><p style="width:320px">Nam libero tempore, cum soluta nobis est eligendi optio cumque nihil imp</p></div>
</section>

<section class="why">
  <h2 class="section-title heading" style="top:76px">WHY CHOOSE US</h2>

  <svg style="position:absolute;left:164px;top:180px" width="50" height="50" viewBox="0 0 24 24"><path d="M21 6.5a5 5 0 0 1-6.6 4.7L5.5 20a1.8 1.8 0 0 1-2.5-2.5l8.8-8.9A5 5 0 0 1 17.5 2l-3 3 .5 3 3 .5z" fill="var(--green)"/></svg>
  <svg style="position:absolute;left:439px;top:182px" width="60" height="46" viewBox="0 0 30 22"><rect x="1" y="2" width="28" height="18" fill="none" stroke="var(--green)" stroke-width="2.5"/><rect x="5" y="5.5" width="20" height="11" fill="var(--green)"/><circle cx="15" cy="11" r="3.5" fill="#fff"/></svg>
  <svg style="position:absolute;left:702px;top:176px" width="56" height="56" viewBox="0 0 24 24" fill="var(--green)"><path d="M9 3h6l3 5-2.5 1.5L12 4.5 9.5 8.5 7 7z"/><path d="M20.5 11 23 15.5 20 20.5h-5v-3h3.5l1.5-2.5-2-3z"/><path d="M3.5 11l2.5 1.5L4 15.5 5.5 18H10v3H4L1 15.5z"/></svg>
  <svg style="position:absolute;left:961px;top:178px" width="54" height="50" viewBox="0 0 24 22"><path d="M12 1 1 11h3v10h6v-6h4v6h6V11h3z" fill="var(--green)"/></svg>

  <div class="feature" style="left:69px;top:270px"><h3>No Maintenance</h3><p>Temporibus autem quibusdam et aut officiis debitis aut rerum neces</p></div>
  <div class="feature" style="left:349px;top:270px"><h3>Save Money</h3><p>Temporibus autem quibusdam et aut officiis debitis aut rerum neces</p></div>
  <div class="feature" style="left:610px;top:270px"><h3>Eco Friendly</h3><p>Temporibus autem quibusdam et aut officiis debitis aut rerum neces</p></div>
  <div class="feature" style="left:868px;top:270px"><h3>Increase Home Energy</h3><p>Temporibus autem quibusdam et aut officiis debitis aut rerum neces</p></div>

  <div class="btn-outline" style="left:520px;top:404px">GET STARTED</div>
</section>

<section class="testimonials" role="img" aria-label="Rooftop solar panels under a dusk sky">
  <svg class="testimonial-panel" width="560" height="374" viewBox="0 0 560 374"><polygon points="0,0 560,0 120,374 0,374" fill="var(--green)"/></svg>
  <svg style="position:absolute;left:98px;top:52px" width="94" height="66" viewBox="0 0 94 66" fill="#fff"><path d="M0 66V34C0 14 10 4 32 0v12C20 16 16 24 16 30h18v36zM56 66V34C56 14 66 4 88 0v12C76 16 72 24 72 30h22v36z"/></svg>
  <div class="quote-label heading">CLIENT<br>TESTIMONIALS</div>
  <p class="testimonial-text">At vero eos et accusamus et iusto odio dignissimos ducimus qui blanditii praesen tium voluptatum deleniti atque corrupti quos dolores et quas molestias excepturi sint occaecati cupiditate non provident, similique sunt..</p>
  <p class="testimonial-name">- JOHN DOE <em>(Manager)</em></p>
  <div class="dots"><span class="on"></span><span></span><span></span></div>
</section>
<div class="avatar" role="img" aria-label="Client portrait"></div>

<footer class="site-footer">
  <div class="footer-brand"><span class="brand-dot"></span><span class="brand-name">Brightfield Energy</span></div>

  <div class="col" style="left:423px">
    <h4>Quick Links</h4>
    <ul><li>Home</li><li>About</li><li>Services</li><li>How it Works</li><li>Blog</li><li>Resources</li><li>Contact</li></ul>
  </div>

  <div class="col" style="left:597px">
    <h4>Newsletter Subscription</h4>
    <p>Register your Email Address to get<br>Information about us</p>
    <div class="email-field">Email Address</div>
    <div class="btn-subscribe">SUBSCRIBE</div>
  </div>

  <div class="col" style="left:922px">
    <h4>Contact Us</h4>
    <div class="contact-row"><svg width="10" height="14" viewBox="0 0 10 14"><path d="M5 0a5 5 0 0 1 5 5c0 4-5 9-5 9S0 9 0 5a5 5 0 0 1 5-5z" fill="var(--blue)"/><circle cx="5" cy="5" r="2" fill="#fff"/></svg><span>2140 Cedar Ridge Avenue,<br>Suite 310<br>Dallas, TX 75204</span></div>
    <div class="contact-row"><svg width="12" height="12" viewBox="0 0 24 24"><path d="M6.6 10.8a15 15 0 0 0 6.6 6.6l2.2-2.2c.3-.3.7-.4 1-.2 1.1.4 2.3.6 3.6.6.6 0 1 .4 1 1V20c0 .6-.4 1-1 1A17 17 0 0 1 3 4c0-.6.4-1 1-1h3.5c.6 0 1 .4 1 1 0 1.3.2 2.5.6 3.6.1.3 0 .7-.2 1z" fill="var(--blue)"/></svg><span>1 800 555 0142</span></div>
    <div class="contact-row"><svg width="14" height="11" viewBox="0 0 14 11"><rect width="14" height="11" rx="1" fill="var(--blue)"/><path d="M1 1.5 7 6l6-4.5" fill="none" stroke="#fff" stroke-width="1.3"/></svg><span>info@brightfieldenergy.com</span></div>
  </div>

  <div class="footer-rule"></div>
  <p class="copyright">Copyrights © 2017, Brightfield Energy.&nbsp; All rights reserved.</p>
  <div class="social"><span></span><span></span><span></span><span></span></div>
</footer>

</body>
</html>
```